Design a business card
Business name: Harbourline Growth Advisory
Improving Business Profitibility

- An Overview of the Business & Service:

Business Performance Consulting

- The Target Market: Small to medium-sized business

- Design Specifics:
White card, blue ink, moon eclipse

No Logo

Target Market(s)

Small to medium-sized business

Font styles to use
Sans Serif

```html
<!DOCTYPE html>
<html lang="en">
<head>
<meta charset="utf-8">
<title>Harbourline Growth Advisory — Business Card</title>
<link rel="stylesheet" href="https://fonts.googleapis.com/css2?family=Oswald:wght@400;500&family=Lato:wght@400&display=swap">
<style>
  :root {
    --backdrop: #2b2b2d;
    --card: #1c1d1f;
    --card-back: #1a1b1d;
    --pattern-tone: #232427;
    --brand-blue: #0b4ea6;
    --ink-white: #f2f2f2;
    --rule: #6a6b6e;
  }
  * { margin: 0; padding: 0; box-sizing: border-box; }
  html, body { width: 1200px; height: 1108px; overflow: hidden; }
  body {
    background: var(--backdrop);
    position: relative;
    font-family: "Lato", sans-serif;
  }
  .card {
    position: absolute;
    top: 204px;
    width: 400px;
    height: 700px;
    border-radius: 24px;
    overflow: hidden;
  }
  .card-front { left: 150px; background: var(--card); text-align: center; }
  .card-back { left: 650px; background: var(--card-back); }

  .brand-mark {
    width: 96px; height: 96px;
    border-radius: 50%;
    background: var(--brand-blue);
    margin: 118px auto 18px;
  }
  .brand-name {
    font-family: "Oswald", sans-serif;
    font-weight: 500;
    color: var(--brand-blue);
    font-size: 34px;
    line-height: 1.05;
    letter-spacing: 0.5px;
    text-transform: uppercase;
  }
  .brand-name .brand-sub { display: block; font-size: 19px; letter-spacing: 7px; margin-top: 2px; }

  .person-name {
    margin-top: 34px;
    font-family: "Oswald", sans-serif;
    font-weight: 400;
    color: var(--brand-blue);
    font-size: 30px;
    text-transform: uppercase;
    line-height: 1.1;
  }
  .person-role { color: var(--ink-white); font-size: 19px; margin-top: 2px; }

  .icon-divider {
    display: flex; align-items: center; justify-content: center;
    gap: 6px; margin: 16px 50px 10px;
  }
  .icon-divider .rule { flex: 1; height: 1px; background: var(--rule); }
  .icon-divider .dot { width: 18px; height: 18px; border-radius: 50%; background: var(--brand-blue); }

  .contact-list { list-style: none; color: var(--ink-white); font-size: 19px; line-height: 1.45; }
  .plain-rule { height: 1px; background: var(--rule); margin: 14px 50px; }
  .address { color: var(--ink-white); font-size: 19px; line-height: 1.4; font-style: normal; }

  .back-pattern {
    position: absolute;
    inset: 0 0 150px 0;
    background: linear-gradient(180deg, var(--pattern-tone) 0%, var(--card-back) 100%);
  }
  .tagline {
    position: absolute;
    left: 54px; bottom: 78px;
    font-family: "Oswald", sans-serif;
    font-weight: 400;
    font-size: 21px;
    letter-spacing: 0.5px;
    color: var(--ink-white);
    text-transform: uppercase;
  }
</style>
</head>
<body>
  <section class="card card-front" aria-label="Business card front">
    <div class="brand-mark" aria-hidden="true"></div>
    <h1 class="brand-name">Harbourline Growth<span class="brand-sub">Advisory</span></h1>
    <h2 class="person-name">Desmond R Akerly</h2>
    <p class="person-role">Managing Director</p>
    <div class="icon-divider" aria-hidden="true">
      <span class="rule"></span><span class="dot"></span><span class="dot"></span><span class="dot"></span><span class="rule"></span>
    </div>
    <ul class="contact-list">
      <li>444 555 0192</li>
      <li>info@harbourlinegrowth.com</li>
      <li>www.harbourlinegrowth.com</li>
    </ul>
    <div class="plain-rule"></div>
    <address class="address">38, Quayside Row,<br>Portmere,60318</address>
  </section>

  <section class="card card-back" aria-label="Business card back">
    <div class="back-pattern" role="img" aria-label="Faint repeating brand pattern in dark grey"></div>
    <p class="tagline">Improving Business Profitibility</p>
  </section>
</body>
</html>
```